Complete Website Redesign

We need a complete revamp of our website. Need to add interactive custmer catalog seection tools. Need to add customer spec input for recommended product search results. Need a cutomer lead and opportunity contact capability. Need a complete Branding message revamp. Primary visuals will be prodcut pictures and case studies.
Target Market(s)
Industrial Customers in the high durability Air movement and fan/blower space; high durability enclosure and flow industries ie. mining, chamicals, manufacturing, water treatment, chemical in use manufacturing
Look and feel
Each slider illustrates characteristics of the customer's brand and the style your logo design should communicate.

```html
<!DOCTYPE html>
<html lang="en">
<head>
<meta charset="utf-8">
<title>Duraflow Composites, LLC</title>
<link href="https://fonts.googleapis.com/css2?family=Source+Sans+3:wght@300;400;600&display=swap" rel="stylesheet">
<style>
:root{
  --brand:#1f3a9e;
  --brand-dark:#0a1a78;
  --nav-top:#2a4bc4;
  --nav-bottom:#13259a;
  --page-grey:#f0f0f0;
  --text:#555;
  --heading:#4a4a4a;
  --frame:#e4e4e4;
  --white:#fff;
  --dot:#4d4d4d;
}
*{margin:0;padding:0;box-sizing:border-box}
html,body{width:998px;height:1200px;overflow:hidden}
body{font-family:"Source Sans 3",sans-serif;color:var(--text);background:var(--white);position:relative}
.top-band{position:absolute;left:0;top:0;width:998px;height:505px;background:var(--page-grey)}
.brand{position:absolute;left:99px;top:40px;display:flex;align-items:center;gap:10px;color:var(--brand);font-weight:600;font-size:19px}
.brand-mark{width:22px;height:22px;background:var(--brand)}
.main-nav{position:absolute;left:99px;top:105px;width:799px;height:51px;background:linear-gradient(var(--nav-top),var(--nav-bottom));border-top:2px solid #5b78e0}
.main-nav a{position:absolute;top:13px;color:var(--white);text-decoration:none;font-size:16px;font-weight:600}
.main-nav .active{left:0;top:0;width:95px;height:49px;background:var(--brand-dark);padding:13px 0 0 40px}
.slider{position:absolute;left:99px;top:164px;width:798px;height:287px;background:var(--frame);padding:6px;box-shadow:0 8px 10px -6px rgba(0,0,0,.35)}
.slide{width:100%;height:100%;background:var(--white);position:relative}
.slide-photo{position:absolute;left:49px;top:21px;width:216px;height:225px;background:linear-gradient(135deg,#e4eaea,#b8c2c4);border-radius:4px}
.slide-text{position:absolute;left:392px;top:95px;width:360px;font-size:15px;font-weight:300;line-height:25px;color:#555}
.dots{position:absolute;left:702px;top:243px;display:flex;gap:4px}
.dots span{width:13px;height:13px;border-radius:50%;background:var(--dot)}
.dots span:first-child{background:var(--brand)}
h2{position:absolute;font-size:16px;font-weight:600;color:var(--heading)}
.intro{position:absolute;left:107px;top:578px;width:517px;font-size:11.7px;line-height:25px;text-align:justify}
.news-item{position:absolute;left:647px;width:270px}
.news-thumb{position:absolute;left:0;top:0;width:74px;height:61px;border:1px solid #ddd;background:linear-gradient(#eef0f0,#c6cccc)}
.news-item p{position:absolute;left:82px;top:-4px;width:187px;font-size:10px;line-height:18.3px;text-align:justify}
.product{position:absolute;top:818px;width:184px}
.product-photo{width:184px;height:113px;border:1px solid #ddd;background:linear-gradient(135deg,#f4f4f4,#b9bec2)}
.product h3{margin-top:11px;font-size:12.5px;font-weight:600;color:var(--heading)}
.product p{margin-top:9px;font-size:10px;line-height:18.3px;text-align:justify}
.product a{display:block;margin-top:10px;font-size:12px;font-weight:600;color:var(--heading);text-decoration:none}
.site-footer{position:absolute;left:0;top:1117px;width:998px;height:83px;background:var(--brand);color:var(--white)}
.footer-nav{position:absolute;left:107px;top:16px;font-size:12.5px}
.footer-nav a{color:var(--white);text-decoration:none}
.footer-nav i{font-style:normal;margin:0 11px}
.copyright{position:absolute;left:107px;top:41px;font-size:12.5px}
.social{position:absolute;left:841px;top:26px;display:flex;gap:4px}
.social span{width:22px;height:22px;border-radius:50%;background:var(--white)}
</style>
</head>
<body>
<div class="top-band"></div>
<header class="brand"><span class="brand-mark"></span>DFC Duraflow Composites, LLC</header>
<nav class="main-nav">
  <a class="active" href="#" style="padding-left:40px">Home</a>
  <a href="#" style="left:107px">Products</a>
  <a href="#" style="left:206px">About Us</a>
  <a href="#" style="left:311px">Mission</a>
  <a href="#" style="left:407px">Request</a>
  <a href="#" style="left:509px">Information</a>
  <a href="#" style="left:633px">Contacts</a>
</nav>
<section class="slider">
  <div class="slide">
    <div class="slide-photo" role="img" aria-label="Fiberglass wall exhaust fan"></div>
    <p class="slide-text">We have a wide selection of fiberglass fans and other corrosion resistant air handling solutions for OEMs, Contractors and Plant Maintenance Operations.</p>
    <div class="dots"><span></span><span></span><span></span><span></span></div>
  </div>
</section>

<h2 style="left:109px;top:535px">Welcome to Duraflow Composites</h2>
<p class="intro">Lorem ipsum dolor sit amet, consectetuer adipiscing elit, sed diam nonummy nibh euismod tincidunt ut laoreet dolore magna aliquam erat volutpat. Ut wisi enim ad minim veniam, quis nostrud exerci tation ullamcorper suscipit lobortis nisl ut aliquip ex ea commodo consequat. Duis autem vel eum iriure dolor in hendrerit in vulputate velit esse molestie consequat, vel illum dolore eu feugiat nulla facilisis at vero eros et accumsan et iusto odio dignissim qui blandit praesent luptatum zzril delenit augue duis dolore te feugait nulla facilisi. Nam liber tempor cum soluta nobis eleifend option congue nihil imperdiet doming id quod mazim placerat facer possim assum.</p>

<h2 style="left:640px;top:535px">Latest News</h2>
<div class="news-item" style="top:583px">
  <div class="news-thumb" role="img" aria-label="Industrial blower units"></div>
  <p>Lorem ipsum dolor sit amet, consectetuer adipiscing elit, sed diam nonummy nibh euismod tincidunt ut laoreet dolore magna aliquam erat volutpat.</p>
</div>
<div class="news-item" style="top:687px">
  <div class="news-thumb" role="img" aria-label="Fiberglass louver panel"></div>
  <p>Lorem ipsum dolor sit amet, consectetuer adipiscing elit, sed diam nonummy nibh euismod tincidunt ut laoreet dolore magna aliquam erat volutpat.</p>
</div>

<h2 style="left:110px;top:783px">Products</h2>
<article class="product" style="left:107px">
  <div class="product-photo" role="img" aria-label="Fiberglass axial propeller fan"></div>
  <h3>Fiberglass Axial Propellers</h3>
  <p>Lorem ipsum dolor sit amet, consectetuer adipiscing elit, sed diam nonummy nibh euismod tincidunt ut laoreet dolore magna aliquam erat volutpat.</p>
  <a href="#">Read More...</a>
</article>
<article class="product" style="left:305px">
  <div class="product-photo" role="img" aria-label="Fiberglass axial duct fan"></div>
  <h3>Fiberglass Axial Fans</h3>
  <p>Lorem ipsum dolor sit amet, consectetuer adipiscing elit, sed diam nonummy nibh euismod tincidunt ut laoreet dolore magna aliquam erat volutpat.</p>
  <a href="#">Read More...</a>
</article>
<article class="product" style="left:507px">
  <div class="product-photo" role="img" aria-label="Fiberglass centrifugal fan"></div>
  <h3>Fiberglass Centrifugal Fans</h3>
  <p>Lorem ipsum dolor sit amet, consectetuer adipiscing elit, sed diam nonummy nibh euismod tincidunt ut laoreet dolore magna aliquam erat volutpat.</p>
  <a href="#">Read More...</a>
</article>
<article class="product" style="left:707px">
  <div class="product-photo" role="img" aria-label="Fiberglass round damper"></div>
  <h3>Fiberglass Louvers and Dampers</h3>
  <p>Lorem ipsum dolor sit amet, consectetuer adipiscing elit, sed diam nonummy nibh euismod tincidunt ut laoreet dolore magna aliquam erat volutpat.</p>
  <a href="#">Read More...</a>
</article>

<footer class="site-footer">
  <nav class="footer-nav"><a href="#">Home</a><i>|</i><a href="#">Products</a><i>|</i><a href="#">About Us</a><i>|</i><a href="#">Mission</a><i>|</i><a href="#">Request</a><i>|</i><a href="#">Information</a><i>|</i><a href="#">Contacts</a></nav>
  <p class="copyright">Copyright ©2013 Company Name &nbsp; - All rights reserved</p>
  <div class="social"><span></span><span></span></div>
</footer>
</body>
</html>
```